Web Site Design For Real Estate Sales Project

The idea behind this project is pretty simple. I am putting my penthouse apartment up for sale and am trying to be creative in selling it.
Technically this will be pretty simple, it will be 3 pages but graphically this has to be as impressive as possible which is why I am trying Pixel Harbor.
The apartment is located in Barra Da Tijuca, Rio De Janeiro, Brazil. (This is where the 2016 Solstice Meet will be held)
I am looking for an index page and 2 sub-pages. I am open to all kinds of designs and navigation's but it has to make an impression quickly with a professional and enticing design. The index page should make it obvious that there is a penthouse apartment for sale in Barra Da Tijuca ( suburb of Rio De Janeiro). The first sub page is about the Condominium where the apartment is located, the second sub page is about the apartment itself.
Here is a more detailed description of what the 3 pages should be about.
Index Page
This is the landing page and should make it obvious that there is an apartment for sale in Barra Da Tijuca, Rio De Janeiro with the following attributes
251 SQ M
Duplex Penthouse
4 suites
Price R$ 2.200.000
Price per SQ M: R$ 8.764
First Sub-Page
This is about the Condominium which is called "Tranquil Cliff Suites" with the following bullets
*Family friendly and safe
*Direct access to the beach
*Many amenities like pool, football court, gym, sauna
There should be some photos of the condominium and a link to the site of the condominium ( www.tcsqv.com )
Second Sub-page
This is about the apartment. It should list in bullets the features of the apartment and then have a photo gallery of the view and various rooms. I have attached sample photos but will eventually have to use more photos.
Apartment Features
Price: R$ 2.220.000
251 m2 Duplex Penthouse
4 suites
maids room with bath
guest bathroom
living room
dinning room
Terrace with heated pool for year round use
Veranda
As mentioned above I am open to all designs and navigation so feel free to be creative. The important thing is catch peoples attention and get the message across in a few seconds, which is that there is an apartment for sale at this price with these features in this location. I will then use zintra clickreach and SEO to get people to the site.
Thanks
Men and Women from 30-60 years of age.
Apartment

```html
<!DOCTYPE html>
<html lang="en">
<head>
<meta charset="utf-8">
<title>Mirante Loft — Apartment for Sale</title>
<link rel="stylesheet" href="https://fonts.googleapis.com/css2?family=PT+Sans:wght@400;700&family=Marcellus&family=Roboto+Condensed:wght@400&family=Arimo:wght@400;700&display=swap">
<style>
  :root {
    --green-deep: #0d2a1f;
    --green-dark: #16402a;
    --green-bright: #7fbf2a;
    --lime: #9ad12e;
    --gold: #f5c000;
    --white: #ffffff;
    --text-soft: #dfe8df;
    --btn-top: #6a6a6a;
    --btn-bottom: #3a3a3a;
    --divider: #4a6a52;
  }
  * { box-sizing: border-box; margin: 0; padding: 0; }
  html, body { width: 1200px; height: 675px; overflow: hidden; }
  body {
    position: relative;
    font-family: "Arimo", Arial, sans-serif;
    color: var(--white);
    background: var(--green-deep);
  }

  /* Header */
  .site-header {
    position: absolute; left: 0; top: 0; width: 1200px; height: 128px;
    background:
      repeating-linear-gradient(90deg, rgba(255,255,255,0.04) 0 18px, rgba(0,0,0,0.05) 18px 36px),
      radial-gradient(ellipse 360px 200px at 630px 20px, #8fc46a 0%, rgba(143,196,106,0) 100%),
      linear-gradient(90deg, #123a33 0%, #3f7a3a 35%, #6aa546 52%, #3f7a3a 70%, #123a33 100%);
    border-bottom: 1px solid #6c9a3c;
  }
  .brand {
    position: absolute; left: 160px; top: 32px;
    font-family: "PT Sans", sans-serif; font-size: 46px; line-height: 50px;
    text-shadow: 2px 3px 4px rgba(0,0,0,0.45);
  }
  .brand-light { color: var(--lime); }
  .brand-bold { color: var(--white); font-weight: 700; }
  .home-icon { position: absolute; left: 558px; top: 38px; }
  .main-nav { position: absolute; top: 45px; left: 622px; display: flex; }
  .nav-button {
    height: 34px; display: flex; align-items: center; justify-content: center;
    font-size: 13px; color: var(--white); text-decoration: none;
    background: linear-gradient(var(--btn-top), var(--btn-bottom));
    border: 1px solid #222; border-radius: 7px;
    box-shadow: inset 0 1px 0 rgba(255,255,255,0.3), 0 2px 3px rgba(0,0,0,0.4);
    white-space: nowrap;
  }
  .nav-suites { width: 168px; }
  .nav-about { width: 138px; margin-left: 16px; }
  .nav-contact { width: 81px; margin-left: 15px; }

  /* Hero */
  .hero {
    position: absolute; left: 0; top: 129px; width: 1200px; height: 463px;
    background:
      repeating-linear-gradient(90deg, rgba(255,255,255,0.025) 0 22px, rgba(0,0,0,0.04) 22px 44px),
      radial-gradient(ellipse 520px 320px at 640px 180px, #3f7a36 0%, rgba(63,122,54,0) 100%),
      linear-gradient(90deg, #081c18 0%, #1c4a2c 40%, #2a5e30 55%, #14382a 80%, #071a16 100%);
  }
  .card-back {
    position: absolute; background: var(--white);
    box-shadow: 4px 6px 10px rgba(0,0,0,0.5);
  }
  .card-back.one { left: 190px; top: 50px; width: 560px; height: 340px; transform: rotate(2.5deg); }
  .card-back.two { left: 186px; top: 44px; width: 556px; height: 336px; transform: rotate(-1.5deg); }
  .card-front {
    position: absolute; left: 185px; top: 57px; width: 557px; height: 334px;
    background: var(--white); box-shadow: 6px 10px 14px rgba(0,0,0,0.55);
  }
  .photo {
    position: absolute; left: 9px; top: 10px; width: 540px; height: 281px;
    background: linear-gradient(180deg, #e4ebee 0%, #b8c3c4 35%, #7c8a78 60%, #9a958a 100%);
  }
  .caption {
    position: absolute; left: 10px; top: 298px;
    font-family: "Roboto Condensed", sans-serif; font-size: 22px; color: #222;
  }
  .slider-dots { position: absolute; left: 400px; top: 426px; display: flex; gap: 10px; }
  .dot { width: 16px; height: 16px; border-radius: 50%; background: var(--white); }
  .dot.active { background: var(--green-bright); }

  .listing { position: absolute; left: 785px; top: 98px; width: 270px; }
  .listing-title {
    font-family: "Marcellus", serif; font-size: 28px; color: var(--gold); line-height: 34px;
  }
  .listing-price { font-size: 24px; font-weight: 700; letter-spacing: 0.8px; margin-top: 1px; }
  .listing-intro { width: 258px; font-size: 12.5px; line-height: 16px; color: var(--text-soft); margin-top: 20px; }
  .location { display: flex; gap: 12px; margin-top: 26px; font-size: 12.5px; line-height: 15px; }
  .location svg { flex: none; }
  .attributes { list-style: none; margin-top: 14px; font-size: 12.5px; line-height: 15px; }
  .attr-label { color: var(--green-bright); }

  /* Footer */
  .site-footer {
    position: absolute; left: 0; top: 592px; width: 1200px; height: 83px;
    background: linear-gradient(90deg, #0a221c, #1a4030 50%, #0a221c);
    border-top: 1px solid #2e5a3a;
  }
  .copyright { position: absolute; left: 160px; top: 14px; font-size: 12.5px; color: var(--text-soft); white-space: nowrap; }
  .copyright strong { font-family: "PT Sans", sans-serif; font-size: 18px; color: var(--white); }
  .divider { position: absolute; top: 8px; width: 1px; height: 70px; background: var(--divider); }
  .contact-row { position: absolute; left: 515px; display: flex; align-items: center; gap: 10px; }
  .contact-label { font-family: "Marcellus", serif; font-size: 18px; color: var(--white); width: 66px; }
  .contact-label span { color: var(--lime); }
  .phone-number { font-size: 25px; font-weight: 700; margin-left: 8px; }
  .email { font-size: 13px; font-weight: 700; margin-left: 8px; }
  .follow { position: absolute; left: 845px; top: 24px; font-family: "Marcellus", serif; font-size: 28px; }
  .follow span { color: var(--lime); }
  .social { position: absolute; left: 988px; top: 27px; display: flex; align-items: center; gap: 8px; }
  .social-dot { width: 24px; height: 24px; border-radius: 50%; background: #3b6fc2; }
  .social-name { font-family: "PT Sans", sans-serif; font-size: 16px; color: var(--white); }
</style>
</head>
<body>
  <header class="site-header">
    <div class="brand"><span class="brand-light">Mirante</span> <span class="brand-bold">Loft</span></div>
    <svg class="home-icon" width="48" height="42" viewBox="0 0 48 42" aria-label="Home">
      <path d="M24 3 L45 22 L40 22 L40 39 L29 39 L29 28 L19 28 L19 39 L8 39 L8 22 L3 22 Z" fill="#e8ece6" stroke="#6a7a66" stroke-width="2" stroke-linejoin="round"/>
    </svg>
    <nav class="main-nav">
      <a class="nav-button nav-suites" href="#">Tranquil Cliff Suites</a>
      <a class="nav-button nav-about" href="#">About the Apartment</a>
      <a class="nav-button nav-contact" href="#">Contact Us</a>
    </nav>
  </header>

  <main class="hero">
    <div class="card-back one"></div>
    <div class="card-back two"></div>
    <figure class="card-front">
      <div class="photo" role="img" aria-label="Terrace with white tables, chairs and parasols beside the pool"></div>
      <figcaption class="caption">Terrace with heated pool for year round use Veranda</figcaption>
    </figure>
    <div class="slider-dots">
      <span class="dot active"></span><span class="dot"></span><span class="dot"></span><span class="dot"></span>
    </div>

    <section class="listing">
      <h1 class="listing-title">Apartment for Sale</h1>
      <p class="listing-price">R$ 2.200.000</p>
      <p class="listing-intro">The apartment is located in Barra Da Tijuca, Rio De Janeiro, Brazil. (This is where the 2016 Solstice Meet will be held)</p>
      <div class="location">
        <svg width="22" height="32" viewBox="0 0 22 32" aria-hidden="true">
          <path d="M11 1 C5 1 1 5.5 1 11 C1 18 11 31 11 31 C11 31 21 18 21 11 C21 5.5 17 1 11 1 Z" fill="#7fbf2a"/>
          <circle cx="11" cy="11" r="4" fill="#16402a"/>
        </svg>
        <p>Barra Da Tijuca, Rio De Janeiro with the following attributes</p>
      </div>
      <ul class="attributes">
        <li><span class="attr-label">Building Size :</span> 251 SQ M</li>
        <li><span class="attr-label">Property Type :</span> Duplex Penthouse</li>
        <li><span class="attr-label">No. of Suites :</span> 4 suites</li>
        <li><span class="attr-label">Price per SQ M :</span> R$ 8.764</li>
      </ul>
    </section>
  </main>

  <footer class="site-footer">
    <p class="copyright"><strong>Mirante Loft</strong> © 2013. All Right Reserved.</p>
    <span class="divider" style="left:483px"></span>
    <div class="contact-row" style="top:10px">
      <svg width="24" height="22" viewBox="0 0 24 22" aria-hidden="true">
        <path d="M2 7 C2 3 6 2 12 2 C18 2 22 3 22 7 L17 8 L16 5 L8 5 L7 8 Z" fill="#7fbf2a"/>
        <path d="M6 10 L18 10 L21 20 L3 20 Z" fill="#7fbf2a"/>
        <circle cx="12" cy="15" r="3" fill="#16402a"/>
      </svg>
      <span class="contact-label">Call <span>us :</span></span>
      <span class="phone-number">712 306 284</span>
    </div>
    <div class="contact-row" style="top:49px">
      <svg width="24" height="18" viewBox="0 0 24 18" aria-hidden="true">
        <rect x="1" y="1" width="22" height="16" fill="#f0c040"/>
        <path d="M1 1 L12 10 L23 1" fill="none" stroke="#b88a10" stroke-width="1.5"/>
      </svg>
      <span class="contact-label">Mail <span>us :</span></span>
      <span class="email">hello@mirante-loft.net</span>
    </div>
    <span class="divider" style="left:820px"></span>
    <p class="follow">Follow <span>us</span></p>
    <div class="social">
      <span class="social-dot"></span>
      <span class="social-name">Linkvale</span>
    </div>
  </footer>
</body>
</html>
```